lantern pathway for children needs a website designer

We need a website designer for our new extension to our company known as 'lantern pathway' providing shadow support services to children based in Singapore. We are a sister branch of a private clinic 'Bright horizons' providing speech language, occupational, and educational therapy to children.

We would like to use our own photos. So the selected design should have a frame with pictures to give us an idea but we will replace them with our own. We will be needing help with inputting information and changing information throughout.

We would like to see designs that are simple, and professional. We have a logo (see attached). The result should convey professionalism in shadow support, fostering independent thinking and moving students towards self-learning.

Target Market(s)

Teachers, psychologists, parents

Industry/Entity Type

Clinic

Requirements
Should not have
• too distracting colours

```html
<!DOCTYPE html>
<html lang="en">
<head>
<meta charset="utf-8">
<title>Lantern Pathway – Shadow Support</title>
<link href="https://fonts.googleapis.com/css2?family=Arimo:wght@400;700&display=swap" rel="stylesheet">
<style>
:root{
  --red:#8a0b0b;
  --red-dark:#6e0505;
  --text:#333;
  --muted:#777;
  --light-bg:#f4f4f4;
  --line:#dcdcdc;
  --footer:#555;
  --white:#fff;
  --grey-btn:#6b6b6b;
}
*{box-sizing:border-box;margin:0;padding:0}
html,body{width:1200px;height:2375px;overflow:hidden}
body{font-family:"Arimo",Arial,sans-serif;color:var(--text);background:var(--white);position:relative}
a{color:inherit;text-decoration:none}

/* header */
.site-header{position:absolute;left:0;top:0;width:1200px;height:108px;background:var(--white)}
.brand{position:absolute;left:133px;top:30px;display:flex;align-items:center;gap:12px}
.brand-mark{width:34px;height:34px;border-radius:50%;background:var(--red)}
.brand-name{font-size:34px;font-weight:700;color:var(--red);letter-spacing:.5px}
.enquiry{position:absolute;left:676px;top:20px;display:flex;align-items:center;gap:10px}
.enquiry-avatar{width:40px;height:44px;border-radius:50%;background:linear-gradient(#d9d9d9,#a9a9a9)}
.enquiry-box{width:144px;height:44px;background:var(--red);border-radius:4px;color:var(--white);text-align:center;padding-top:5px}
.enquiry-box .lbl{font-size:11px;display:block}
.enquiry-box .num{font-size:15px;display:block;margin-top:3px}
.register-btn{position:absolute;left:902px;top:20px;width:166px;height:42px;background:var(--grey-btn);border-radius:5px;color:var(--white);font-size:18px;text-align:center;line-height:42px;letter-spacing:.5px}
.header-email{position:absolute;right:132px;top:84px;font-size:11px;color:#555}

/* nav */
.main-nav{position:absolute;left:0;top:108px;width:1200px;height:48px;background:linear-gradient(#9d1212,var(--red-dark));border-top:2px solid #b01515}
.main-nav a{position:absolute;top:14px;color:var(--white);font-size:15px}
.search{position:absolute;left:898px;top:10px;width:170px;height:26px;background:var(--white);border:1px solid #bbb}
.search svg{position:absolute;right:6px;top:5px}

/* hero */
.hero{position:absolute;left:0;top:156px;width:1200px;height:559px;background:linear-gradient(160deg,#e9d7c7 0%,#c9a88f 35%,#b83a2e 70%,#8a7e7c 100%)}
.hero-arrow{position:absolute;top:229px;width:48px;height:48px;border-radius:50%;background:rgba(60,60,60,.75)}
.hero-arrow.next{background:var(--red)}
.hero-caption{position:absolute;left:130px;top:426px;width:940px;height:95px;background:rgba(255,255,255,.82);border-radius:3px}
.hero-caption p{position:absolute;left:20px;top:15px;width:700px;font-size:16px;line-height:33px;color:#333}
.btn-red{display:block;background:var(--red);color:var(--white);font-size:12px;text-align:center}
.hero-caption .btn-red{position:absolute;left:793px;top:32px;width:106px;height:30px;line-height:30px;border-radius:3px}

/* about */
.about{position:absolute;left:0;top:715px;width:1200px;height:312px;background:var(--light-bg)}
.section-title{position:absolute;left:0;width:1200px;text-align:center;font-size:24px;color:#3c3c3c}
.section-sub{position:absolute;left:0;width:1200px;text-align:center;font-size:11px;color:var(--muted)}
.about-item{position:absolute;top:105px;width:280px;text-align:center}
.about-icon{width:82px;height:82px;border-radius:50%;border:3px solid #cfcfcf;background:var(--white);margin:0 auto;display:flex;align-items:center;justify-content:center}
.about-item h3{font-size:15px;font-weight:400;color:#222;margin-top:18px}
.about-item p{font-size:11.5px;line-height:21px;color:var(--muted);margin-top:10px}

/* services */
.service{position:absolute;top:1133px;width:291px}
.service-photo{width:291px;height:205px;border:1px solid var(--line)}
.service p{font-size:11.5px;line-height:24px;color:var(--muted);margin-top:10px;height:82px}
.service .btn-red{width:118px;height:36px;line-height:36px;margin-top:6px}

/* shadow support */
.support{position:absolute;left:133px;top:1493px;width:935px;height:344px;background:var(--light-bg);border:1px solid var(--line)}
.support h2{position:absolute;left:19px;top:20px;font-size:17px;font-weight:400;color:var(--red)}
.support-card{position:absolute;top:59px;width:436px;height:268px;background:var(--white);border:1px solid var(--line);padding:16px 17px 0 17px}
.support-card h4{font-size:12.5px;font-weight:400;color:var(--red)}
.support-card p{font-size:11px;line-height:26px;color:#555;margin-top:6px}
.support-card ul{list-style:none;margin-top:4px}
.support-card li{font-size:11px;line-height:27px;color:#555;padding-left:32px;position:relative}
.support-card li svg{position:absolute;left:10px;top:5px}
.more-link{display:block;font-size:12px;color:var(--red);margin-top:10px}

/* audience cards */
.audience{position:absolute;top:1867px;width:291px;height:355px;border:1px solid var(--line)}
.audience-photo{width:289px;height:203px}
.audience-body{position:absolute;left:0;top:203px;width:289px;height:150px;background:var(--red);padding:16px 17px 0 17px;color:var(--white)}
.audience-body h4{font-size:13px;font-weight:700}
.audience-body p,.audience-body .sub-link{display:block;font-size:11px;line-height:23px;margin-top:4px}
.audience-body .sub-link{text-decoration:underline;margin-top:0}
.audience-body .btn-white{position:absolute;left:17px;top:97px;width:118px;height:36px;line-height:36px;background:var(--white);color:var(--red);font-size:13px;text-align:center;text-decoration:none}

/* footer */
.site-footer{position:absolute;left:0;top:2253px;width:1200px;height:122px;background:var(--footer)}
.site-footer nav a{position:absolute;top:38px;color:var(--white);font-size:15px}
.copyright{position:absolute;left:133px;top:82px;font-size:11px;color:#ddd}
.social{position:absolute;top:42px;width:38px;height:38px;border-radius:50%;background:#e8e8e8}
</style>
</head>
<body>

<header class="site-header">
  <div class="brand"><span class="brand-mark"></span><span class="brand-name">Lantern Pathway</span></div>
  <div class="enquiry">
    <div class="enquiry-avatar" role="img" aria-label="Support agent portrait"></div>
    <div class="enquiry-box"><span class="lbl">Make An Enquiry</span><span class="num">+65 6100 2480</span></div>
  </div>
  <a class="register-btn" href="#">Register Shadow</a>
  <div class="header-email">enquiries@brightvaleclinic.example</div>
</header>

<nav class="main-nav">
  <a href="#" style="left:133px">About Us</a>
  <a href="#" style="left:235px">Mission</a>
  <a href="#" style="left:328px">Our Services</a>
  <a href="#" style="left:456px">Shadow Support</a>
  <a href="#" style="left:613px">Contact Us</a>
  <div class="search">
    <svg width="16" height="16" viewBox="0 0 16 16"><circle cx="6" cy="6" r="4.5" fill="none" stroke="#555" stroke-width="2"/><line x1="9.5" y1="9.5" x2="14" y2="14" stroke="#555" stroke-width="2.5"/></svg>
  </div>
</nav>

<section class="hero" role="img" aria-label="Classroom photo: teacher standing with children seated on the floor">
  <a class="hero-arrow prev" href="#" style="left:19px"><svg width="48" height="48" viewBox="0 0 48 48"><polyline points="28,14 18,24 28,34" fill="none" stroke="#fff" stroke-width="5"/></svg></a>
  <a class="hero-arrow next" href="#" style="left:1134px"><svg width="48" height="48" viewBox="0 0 48 48"><polyline points="20,14 30,24 20,34" fill="none" stroke="#fff" stroke-width="5"/></svg></a>
  <div class="hero-caption">
    <p>Lantern Pathway is part of the Brightvale Clinic Group of Companies, who are<br>providing speech language therapy, occupational therapy and educational therapy services</p>
    <a class="btn-red" href="#">Read More &gt;&gt;</a>
  </div>
</section>

<section class="about">
  <h2 class="section-title" style="top:26px">ABOUT US</h2>
  <p class="section-sub" style="top:66px">Lantern Pathway is part of the Brightvale Clinic Group of Companies, who are providing</p>

  <div class="about-item" style="left:138px">
    <div class="about-icon"><svg width="46" height="40" viewBox="0 0 46 40"><ellipse cx="20" cy="16" rx="18" ry="13" fill="#8a0b0b"/><path d="M10 26 L6 36 L18 28Z" fill="#8a0b0b"/><ellipse cx="32" cy="22" rx="12" ry="9" fill="#8a0b0b" stroke="#fff" stroke-width="2"/></svg></div>
    <h3>Speech Language Therapy</h3>
    <p>Lantern Pathway aims to work in an integrated manner, respecting the work of the respective professionals involved</p>
  </div>
  <div class="about-item" style="left:457px">
    <div class="about-icon"><svg width="44" height="44" viewBox="0 0 44 44" fill="none" stroke="#8a0b0b" stroke-width="3"><path d="M10 4 V16 a8 8 0 0 0 16 0 V4"/><path d="M18 24 V32 a8 8 0 0 0 16 0 V26"/><circle cx="34" cy="22" r="4"/></svg></div>
    <h3>Occupational Therapy</h3>
    <p>Lantern Pathway aims to work in an integrated manner, respecting the work of the respective professionals involved</p>
  </div>
  <div class="about-item" style="left:778px">
    <div class="about-icon"><svg width="48" height="36" viewBox="0 0 48 36"><polygon points="24,2 46,12 24,22 2,12" fill="#8a0b0b"/><path d="M12 17 V26 c6 6 18 6 24 0 V17 L24 23Z" fill="#8a0b0b"/><line x1="42" y1="13" x2="42" y2="26" stroke="#8a0b0b" stroke-width="2"/></svg></div>
    <h3>Educational therapy</h3>
    <p>Lantern Pathway aims to work in an integrated manner, respecting the work of the respective professionals involved</p>
  </div>
</section>

<h2 class="section-title" style="top:1051px">OUR SERVICES</h2>
<p class="section-sub" style="top:1092px">We provide a full fledged, seamless service that serves to:</p>

<div class="service" style="left:133px">
  <div class="service-photo" role="img" aria-label="Photo of a child playing with building blocks beside a carer" style="background:linear-gradient(135deg,#d9c3ad,#b8a2c9)"></div>
  <p>Train shadows with a strong focus on equipping them with dynamic, clinical skills.</p>
  <a class="btn-red" href="#">Read More &gt;&gt;</a>
</div>
<div class="service" style="left:455px">
  <div class="service-photo" role="img" aria-label="Photo of a therapist helping a child on climbing equipment" style="background:linear-gradient(135deg,#c9a48a,#7f9fb8)"></div>
  <p>Provide families with well-trained Shadows who are mentored by Speech Language Pathologists and Professional Therapists to carry out shadow support.</p>
  <a class="btn-red" href="#">Read More &gt;&gt;</a>
</div>
<div class="service" style="left:776px">
  <div class="service-photo" role="img" aria-label="Photo of an educator reading with a young girl" style="background:linear-gradient(135deg,#b9c79d,#d9b89b)"></div>
  <p style="text-align:justify">Work with educational professionals (Educational Psychologists) to provide an effective solution to the learning needs of a student.</p>
  <a class="btn-red" href="#">Read More &gt;&gt;</a>
</div>

<section class="support">
  <h2>SHADOW SUPPORT</h2>
  <div class="support-card" style="left:21px">
    <h4>What is shadow support?</h4>
    <p>A shadow support is para-professional who can help a struggling student to integrate and learn in their school environment....................</p>
    <ul>
      <li><svg width="14" height="14" viewBox="0 0 14 14"><polyline points="1,7 5,12 13,1" fill="none" stroke="#8a0b0b" stroke-width="2.5"/></svg>Have difficulties in integrating learning in classroom</li>
      <li><svg width="14" height="14" viewBox="0 0 14 14"><polyline points="1,7 5,12 13,1" fill="none" stroke="#8a0b0b" stroke-width="2.5"/></svg>Have social challenges and find it difficult to connect with peers</li>
      <li><svg width="14" height="14" viewBox="0 0 14 14"><polyline points="1,7 5,12 13,1" fill="none" stroke="#8a0b0b" stroke-width="2.5"/></svg>Have difficulties in understanding instructions</li>
    </ul>
    <p style="margin-top:14px">A central goal of the shadow support would be to help the student achieve.......</p>
    <a class="more-link" href="#" style="margin-top:4px">{ Read More &gt;&gt; }</a>
  </div>
  <div class="support-card" style="left:482px">
    <h4>What are its Advantages?</h4>
    <p>A fully trained shadow support is an asset to the student who otherwise would have trouble fitting in and adapting to the mainstream school environment.</p>
    <a class="more-link" href="#">{ Read More &gt;&gt; }</a>
    <h4 style="margin-top:22px">How do I know if my child needs shadowing</h4>
    <p>A consultation with our Speech Language Pathologist, along with an assessment by an Educational .................</p>
    <a class="more-link" href="#" style="margin-top:4px">{ Read More &gt;&gt; }</a>
  </div>
</section>

<div class="audience" style="left:133px">
  <div class="audience-photo" role="img" aria-label="Photo of a parent helping a child with homework" style="background:linear-gradient(135deg,#e4d6c7,#7f9cc4)"></div>
  <div class="audience-body">
    <h4>How You Can Collaborate With Us</h4>
    <p>Shadow Support will participate in a collaborative working relationship with the professionals working</p>
    <a class="btn-white" href="#">Read More &gt;&gt;</a>
  </div>
</div>
<div class="audience" style="left:454px">
  <div class="audience-photo" role="img" aria-label="Photo of a child playing with blocks beside a parent" style="background:linear-gradient(135deg,#d9c3ad,#b8a2c9)"></div>
  <div class="audience-body">
    <h4>For Parents</h4>
    <a class="sub-link" href="#" style="margin-top:6px">Registration Form</a>
    <a class="sub-link" href="#">Cost Estimation</a>
    <a class="btn-white" href="#">Read More &gt;&gt;</a>
  </div>
</div>
<div class="audience" style="left:776px">
  <div class="audience-photo" role="img" aria-label="Photo of a class of pupils in red uniforms raising their hands" style="background:linear-gradient(135deg,#c8b09a,#b8403a)"></div>
  <div class="audience-body">
    <h4>For Schools</h4>
    <p>How Do We Help You Achieve Your Goals</p>
    <p style="margin-top:0">How Do I Know If My Child Needs Support</p>
    <a class="btn-white" href="#">Read More &gt;&gt;</a>
  </div>
</div>

<footer class="site-footer">
  <nav>
    <a href="#" style="left:133px">About Us</a>
    <a href="#" style="left:224px">Mission</a>
    <a href="#" style="left:304px">Our Services</a>
    <a href="#" style="left:420px">Shadow Support</a>
    <a href="#" style="left:564px">Contact Us</a>
  </nav>
  <p class="copyright">©2014 all copyrights are reserved</p>
  <span class="social" style="left:826px" aria-label="Social link"></span>
  <span class="social" style="left:877px" aria-label="Social link"></span>
  <span class="social" style="left:926px" aria-label="Social link"></span>
  <span class="social" style="left:975px" aria-label="Social link"></span>
  <span class="social" style="left:1026px" aria-label="Social link"></span>
</footer>

</body>
</html>
```